showcase project portfolio

create power point of project portfolio
from word file and website using similar design template

https://www.brelmor.co.uk/

Target Market(s)

corporte

```html
<!DOCTYPE html>
<html lang="en">
<head>
<meta charset="utf-8">
<title>Brelmor Project Portfolio</title>
<link rel="stylesheet" href="https://fonts.googleapis.com/css2?family=Montserrat:wght@600;700&family=Lato:wght@400;700&display=swap">
<style>
:root{
  --stage:#c8c8c8;
  --paper:#ffffff;
  --navy:#1f3a52;
  --ink:#2a3d52;
  --tan:#c9a98e;
  --text:#333a42;
  --brick:#9b5a42;
  --green:#5f7f3e;
  --sky:#d9dee2;
}
*{box-sizing:border-box;margin:0;padding:0}
html,body{width:1200px;height:367px;overflow:hidden;background:var(--stage)}
body{position:relative;font-family:"Lato",sans-serif;color:var(--text)}
.slide{position:absolute;width:283px;height:159px;background:var(--paper);overflow:hidden;box-shadow:0 1px 2px rgba(0,0,0,.15)}
.slide::after{content:"";position:absolute;left:0;right:0;bottom:0;height:3px;background:linear-gradient(90deg,var(--tan) 50%,var(--navy) 50%)}
.notch{position:absolute;left:50%;top:0;transform:translateX(-50%);width:0;height:0;border-left:4px solid transparent;border-right:4px solid transparent;border-top:6px solid var(--navy)}
.title{position:absolute;left:0;right:0;text-align:center;font-family:"Montserrat",sans-serif;font-weight:700;color:var(--ink);font-size:7.5px;letter-spacing:.1px}
.date,.page{position:absolute;bottom:6px;font-family:"Montserrat",sans-serif;font-weight:700;font-size:3.2px}
.date{left:14px;color:var(--ink)}
.page{right:14px;color:var(--tan)}
.line{position:absolute;left:0;right:0;text-align:center;font-size:4px;color:var(--text)}
.line b{font-weight:700;margin-right:3px}
.media{position:absolute}
.photo-brick{background:linear-gradient(160deg,#7d4a38,#a4674f 55%,#5d6b48)}
.photo-street{background:linear-gradient(170deg,#b9c0c4,#8c6a58 50%,#5a5a5a)}
.photo-tree{background:linear-gradient(160deg,#4f6b3a,#7a5a44 60%,#a59a8c)}
.drawing{background:linear-gradient(135deg,#f4f4f0,#e7e9e4);border:.5px solid #ddd}
.drawing-colour{background:linear-gradient(135deg,#f3f1c8,#eef0f4 60%,#f2e3e3);border:.5px solid #ddd}

/* welcome */
.welcome-name{position:absolute;left:88px;top:136px;font-family:"Montserrat",sans-serif;font-weight:700;font-size:10px;color:var(--ink)}
.brand{position:absolute;font-family:"Montserrat",sans-serif;font-weight:700;color:var(--navy)}

/* tasks */
.tasks-head{position:absolute;left:14px;top:40px;font-family:"Montserrat",sans-serif;font-weight:700;font-size:4.6px;color:var(--tan)}
.task-list{position:absolute;list-style:none;font-size:3.4px;color:var(--text)}
.task-list li{display:flex;gap:3px;height:11px;align-items:flex-start}
.task-list svg{flex:none;width:3.5px;height:3.5px}
.divider{position:absolute;left:132px;top:42px;width:.5px;height:100px;background:#e2e2e2}

/* contact */
.contact-bg{position:absolute;inset:0;background:radial-gradient(circle at 30% 40%,#ffffff,#f1f2f4 75%)}
.contact-col{position:absolute;left:160px;top:32px;width:.5px;height:110px;background:#e0e0e0}
.contact-item{position:absolute;left:170px;display:flex;gap:6px;align-items:flex-start}
.contact-item .icon{width:14px;height:14px;border-radius:50%;background:var(--tan);display:flex;align-items:center;justify-content:center;flex:none}
.contact-label{font-size:2.4px;font-weight:700;color:var(--ink);letter-spacing:.2px}
.contact-value{font-size:4px;font-weight:700;color:var(--ink);line-height:1.6}
.thanks{position:absolute;left:40px;width:100px;text-align:center;top:113px;font-family:"Montserrat",sans-serif;font-weight:700;font-size:7px;color:var(--tan)}
</style>
</head>
<body>

<!-- Slide 1: welcome -->
<section class="slide" style="left:12.6px;top:13px">
  <svg class="media" width="283" height="159" viewBox="0 0 283 159" role="img" aria-label="Photograph of a red brick detached house with lawn and patio">
    <defs>
      <linearGradient id="houseGrad" x1="0" y1="0" x2="0" y2="1">
        <stop offset="0" stop-color="#c9d2d8"/>
        <stop offset=".45" stop-color="#a4634a"/>
        <stop offset=".75" stop-color="#8b5a43"/>
        <stop offset="1" stop-color="#4f8a2e"/>
      </linearGradient>
    </defs>
    <path d="M0 0H283V100Q200 108 140 128Q60 112 0 104Z" fill="url(#houseGrad)"/>
    <path d="M0 104Q60 112 140 128Q200 108 283 100V105Q200 112 140 133Q60 117 0 109Z" fill="var(--tan)"/>
  </svg>
  <div class="brand" style="left:14px;top:138px;font-size:6px">brelmor</div>
  <div class="welcome-name">WELCOME TO BRELMOR</div>
</section>

<!-- Slide 2: tasks -->
<section class="slide" style="left:310px;top:13px">
  <span class="notch"></span>
  <h1 class="title" style="top:12px;line-height:12px">PROJECTS MANAGED BY BRELMOR DESIGN<br>SOLUTIONS LTD</h1>
  <div class="tasks-head">TASKS</div>
  <ul class="task-list" style="left:14px;top:52px;width:112px">
    <li><svg viewBox="0 0 10 10"><path d="M1 5l3 3 5-7" fill="none" stroke="var(--tan)" stroke-width="2"/></svg>Creating working drawings</li>
    <li><svg viewBox="0 0 10 10"><path d="M1 5l3 3 5-7" fill="none" stroke="var(--tan)" stroke-width="2"/></svg>Price breakdown of total build costs</li>
    <li style="height:22px"><svg viewBox="0 0 10 10"><path d="M1 5l3 3 5-7" fill="none" stroke="var(--tan)" stroke-width="2"/></svg><span style="line-height:11px;margin-top:-3.8px">Liaising with Vale River Waters for water connection,<br>drainage connection</span></li>
    <li><svg viewBox="0 0 10 10"><path d="M1 5l3 3 5-7" fill="none" stroke="var(--tan)" stroke-width="2"/></svg>Liaising with Hearthline gas to get gas supply to site</li>
    <li><svg viewBox="0 0 10 10"><path d="M1 5l3 3 5-7" fill="none" stroke="var(--tan)" stroke-width="2"/></svg>Liaising with Northway Power to get electric supply</li>
    <li><svg viewBox="0 0 10 10"><path d="M1 5l3 3 5-7" fill="none" stroke="var(--tan)" stroke-width="2"/></svg>Tendering out works to different tradesman</li>
    <li><svg viewBox="0 0 10 10"><path d="M1 5l3 3 5-7" fill="none" stroke="var(--tan)" stroke-width="2"/></svg>Getting material orders</li>
  </ul>
  <span class="divider"></span>
  <ul class="task-list" style="left:149px;top:58px;width:130px">
    <li><svg viewBox="0 0 10 10"><path d="M1 5l3 3 5-7" fill="none" stroke="var(--tan)" stroke-width="2"/></svg>Arranging structural engineer for the site</li>
    <li><svg viewBox="0 0 10 10"><path d="M1 5l3 3 5-7" fill="none" stroke="var(--tan)" stroke-width="2"/></svg>Arranging Building control for the site</li>
    <li><svg viewBox="0 0 10 10"><path d="M1 5l3 3 5-7" fill="none" stroke="var(--tan)" stroke-width="2"/></svg>Making sure material is on site on time</li>
    <li><svg viewBox="0 0 10 10"><path d="M1 5l3 3 5-7" fill="none" stroke="var(--tan)" stroke-width="2"/></svg>Making sure all tradesman work is up to current British standards</li>
    <li><svg viewBox="0 0 10 10"><path d="M1 5l3 3 5-7" fill="none" stroke="var(--tan)" stroke-width="2"/></svg>Daily walk rounds to check work is done according to approved plans</li>
    <li><svg viewBox="0 0 10 10"><path d="M1 5l3 3 5-7" fill="none" stroke="var(--tan)" stroke-width="2"/></svg>Placing orders for bathrooms, kitchen, and flooring</li>
    <li><svg viewBox="0 0 10 10"><path d="M1 5l3 3 5-7" fill="none" stroke="var(--tan)" stroke-width="2"/></svg>All snag work with main contactor</li>
  </ul>
  <span class="date">04 JUNE 2024</span><span class="page">PAGE NO: 02</span>
</section>

<!-- Slide 3: project one -->
<section class="slide" style="left:608px;top:13px">
  <span class="notch"></span>
  <h2 class="title" style="top:14px">PROJECT ONE</h2>
  <p class="line" style="top:31px;font-family:'Montserrat',sans-serif;font-weight:700;color:var(--ink);font-size:3.8px">GARAGES AT ASHCROFT MEWS, ASHCROFT STREET, DERBY</p>
  <p class="line" style="top:41px;line-height:9px">Proposal: Change of use from garages to two dwelling houses (use class C3) including alterations to<br>the front and side elevations</p>
  <div class="media photo-brick" style="left:14px;top:67px;width:81px;height:64px" role="img" aria-label="Photograph of existing brick garages"></div>
  <div class="media photo-street" style="left:104px;top:67px;width:81px;height:64px" role="img" aria-label="Photograph of converted mews houses"></div>
  <div class="media drawing-colour" style="left:193px;top:66px;width:77px;height:64px" role="img" aria-label="Floor plans and elevation drawings"></div>
  <span class="date">04 JUNE 2024</span><span class="page">PAGE NO: 03</span>
</section>

<!-- Slide 4: project 2 -->
<section class="slide" style="left:906px;top:13px">
  <span class="notch"></span>
  <h2 class="title" style="top:14px">PROJECT 2</h2>
  <div class="media photo-tree" style="left:14px;top:32px;width:81px;height:65px" role="img" aria-label="Photograph of office building behind a tree"></div>
  <div class="media photo-brick" style="left:104px;top:45px;width:81px;height:65px" role="img" aria-label="Photograph of brick office building front"></div>
  <div class="media drawing" style="left:193px;top:66px;width:77px;height:52px" role="img" aria-label="Floor plan drawings for flats"></div>
  <p class="line" style="top:127px">Proposal: Change of use from offices (use class B1) to 12 flats (use class C3)</p>
  <span class="date">04 JUNE 2024</span><span class="page">PAGE NO: 04</span>
</section>

<!-- Slide 5: project 3 -->
<section class="slide" style="left:12.6px;top:190px">
  <span class="notch"></span>
  <h2 class="title" style="top:14px">PROJECT 3</h2>
  <p class="line" style="top:30px;text-align:left;left:26px"><b>Location:</b> 12-16 Mill Lane Derby &nbsp;&nbsp;&nbsp;&nbsp; <b>Proposal:</b> Refurbishment Of Commercial Ground Floor Units Together With</p>
  <p class="line" style="top:40px">Formation Of 6 Residential Units On First And Second Floors. Installation Of Glazing And</p>
  <div class="media photo-street" style="left:14px;top:55px;width:81px;height:64px" role="img" aria-label="Photograph of commercial building on a street corner"></div>
  <div class="media photo-street" style="left:103px;top:55px;width:81px;height:64px" role="img" aria-label="Photograph of the building from another angle"></div>
  <div class="media drawing-colour" style="left:193px;top:72px;width:77px;height:31px" role="img" aria-label="Coloured floor plans"></div>
  <p class="line" style="top:128px">Repair To External Masonry Including Bricking Up Of Existing Openings</p>
  <span class="date">04 JUNE 2024</span><span class="page">PAGE NO: 05</span>
</section>

<!-- Slide 6: project 4 -->
<section class="slide" style="left:310px;top:190px">
  <span class="notch"></span>
  <h2 class="title" style="top:13px">PROJECT 4</h2>
  <p class="line" style="top:32px"><b>Location:</b> &nbsp;&nbsp; Land At 4 Orchard Close Derby DE21 9QX &nbsp;&nbsp;&nbsp;&nbsp; <b>Proposal:</b> &nbsp;&nbsp; Erection of a dwelling house (use class C3)</p>
  <div class="media photo-brick" style="left:14px;top:50px;width:255px;height:80px" role="img" aria-label="Photograph of completed new brick and render house with cars on drive"></div>
  <span class="date">04 JUNE 2024</span><span class="page">PAGE NO: 06</span>
</section>

<!-- Slide 7: project 5 -->
<section class="slide" style="left:608px;top:190px">
  <span class="notch"></span>
  <h2 class="title" style="top:14px">PROJECT 5</h2>
  <p class="line" style="top:30px"><b style="font-weight:400">Location: 41, Kelso Street, Birmingham</b> &nbsp;&nbsp;&nbsp;&nbsp;&nbsp;&nbsp; <b>Proposal:</b> Warehouse conversion to 4 town houses.</p>
  <div class="media photo-tree" style="left:15px;top:42px;width:72px;height:45px" role="img" aria-label="Photograph of overgrown site"></div>
  <div class="media drawing" style="left:92px;top:42px;width:75px;height:45px" role="img" aria-label="Proposed front elevation drawing"></div>
  <div class="media drawing" style="left:175px;top:42px;width:56px;height:45px" role="img" aria-label="Floor plan drawings"></div>
  <div class="media photo-street" style="left:236px;top:42px;width:33px;height:45px" role="img" aria-label="Photograph of side alley of warehouse"></div>
  <div class="media photo-brick" style="left:87px;top:96px;width:50px;height:45px" role="img" aria-label="Photograph of warehouse facade"></div>
  <div class="media photo-brick" style="left:147px;top:96px;width:50px;height:45px" role="img" aria-label="Photograph of warehouse entrance"></div>
  <span class="date">04 JUNE 2024</span><span class="page">PAGE NO: 07</span>
</section>

<!-- Slide 8: contact -->
<section class="slide" style="left:906px;top:190px">
  <div class="contact-bg"></div>
  <span class="notch"></span>
  <h2 class="title" style="top:12px">GET IN TOUCH WITH US</h2>
  <div class="brand" style="left:40px;width:100px;text-align:center;top:70px;font-size:16px">brelmor</div>
  <div class="thanks">THANK YOU</div>
  <span class="contact-col"></span>
  <div class="contact-item" style="top:38px">
    <span class="icon"><svg width="6" height="6" viewBox="0 0 24 24"><path d="M6.6 10.8a15 15 0 006.6 6.6l2.2-2.2a1 1 0 011-.25 11.4 11.4 0 003.6.6 1 1 0 011 1V20a1 1 0 01-1 1A17 17 0 013 4a1 1 0 011-1h3.5a1 1 0 011 1 11.4 11.4 0 00.6 3.6 1 1 0 01-.25 1z" fill="#fff"/></svg></span>
    <div><div class="contact-label">PHONE NUMBER:</div><div class="contact-value">+44 7700900123<br>+44 7700900456</div></div>
  </div>
  <div class="contact-item" style="top:70px">
    <span class="icon"><svg width="6" height="6" viewBox="0 0 24 24"><path d="M2 5h20v14H2z" fill="#fff"/><path d="M2 5l10 8 10-8" fill="none" stroke="var(--tan)" stroke-width="2"/></svg></span>
    <div><div class="contact-label">MAIL US:</div><div class="contact-value">info@brelmor.co.uk</div></div>
  </div>
  <div class="contact-item" style="top:100px">
    <span class="icon"><svg width="6" height="6" viewBox="0 0 24 24"><path d="M12 2a7 7 0 00-7 7c0 5 7 13 7 13s7-8 7-13a7 7 0 00-7-7zm0 9.5A2.5 2.5 0 1112 6.5a2.5 2.5 0 010 5z" fill="#fff"/></svg></span>
    <div><div class="contact-label">LOCATION:</div><div class="contact-value">Elmfield Road, Brookhurst,<br>Derby DE22 0ZZ</div></div>
  </div>
  <span class="date">04 JUNE 2024</span><span class="page">PAGE NO: 08</span>
</section>

</body>
</html>
```